Wellbrook Talking Therapies Hub Swindon

We need a design for magazine advert, ideally high resolution to advertise our counselling centre. we would like this to include a photo of two people talking, as if in a counselling session. See our logo and colour range on our website. www.wbtth-swindon.co.uk
The photo should not include cups of coffee, clipboards, desks, people touching. it needs to be two people in armchairs sympathetically listening and looking at each other.
The font type is Great Vibes on the logo. Our design should communicate a centre of excellence delivering high quality, professional services in stylishly furnished surroundings.

Hello Everyone We have had a number of designs that look quite promising but are missing the brief. Can I reiterate that we need a photograph of 2 people seated talking to each other in a sincere way. There shouldn't be office chairs but comfortable chairs. There should be no physical contact. There should be no clipboards.Thank you very muchHeather Added Sunday, March 12, 2017

Target Market(s)

people seeking counselling and psychotherapy

Font styles to use
Other font styles liked:
• Great Vibes as in our logo for some of the print. See attached file.

Requirements
Must have
• good photograph
• Two high res Pixavend photos:
• https://pixavend-files.example-cdn.net/download?id=a81kd93jf02mdl47xq
• https://pixavend-files.example-cdn.net/download?id=z57pw20ne84bvc13ty
Nice to have
• Watermark in keeping with our logo.
Should not have
• Darkness

```html
<!DOCTYPE html>
<html lang="en">
<head>
<meta charset="utf-8">
<title>Wellbrook Talking Therapies Hub – Magazine Advert</title>
<link href="https://fonts.googleapis.com/css2?family=Great+Vibes&family=Montserrat:wght@400;500;600&display=swap" rel="stylesheet">
<style>
  :root {
    --page-bg: #ececec;
    --cream: #f3eedc;
    --sage: #a9bf8c;
    --olive: #7f9a2e;
    --green-text: #7aa060;
    --brown: #3f3431;
    --ink: #2e2624;
    --white: #ffffff;
  }
  * { margin: 0; padding: 0; box-sizing: border-box; }
  html, body { width: 1200px; height: 1200px; overflow: hidden; }
  body {
    background: var(--page-bg);
    font-family: "Montserrat", Arial, sans-serif;
    color: var(--ink);
  }
  .advert {
    position: absolute;
    left: 210px;
    top: 50px;
    width: 780px;
    height: 1100px;
    overflow: hidden;
    background: var(--white);
    box-shadow: 0 10px 30px rgba(0,0,0,0.12);
  }
  .advert-shapes { position: absolute; inset: 0; width: 780px; height: 1100px; }
  .headline {
    position: absolute;
    left: 0;
    top: 488px;
    width: 780px;
    text-align: center;
    font-family: "Great Vibes", cursive;
    font-weight: 400;
    font-size: 52px;
    line-height: 60px;
    color: var(--ink);
  }
  .intro {
    position: absolute;
    left: 162px;
    top: 662px;
    width: 330px;
    font-size: 16.5px;
    line-height: 23px;
    color: var(--ink);
  }
  .intro .highlight { color: var(--olive); font-weight: 500; }
  .contact {
    position: absolute;
    left: 64px;
    top: 912px;
    width: 300px;
    color: var(--white);
  }
  .contact .hours { font-size: 14.5px; line-height: 17px; }
  .contact .phone {
    font-size: 31px;
    line-height: 36px;
    color: var(--green-text);
    margin-top: 2px;
    letter-spacing: 0.5px;
  }
  .contact .address { font-size: 14px; line-height: 17px; margin-top: 12px; }
  .contact .website { font-size: 14px; font-weight: 600; margin-top: 17px; }
  .brand-name {
    position: absolute;
    left: 360px;
    top: 978px;
    width: 410px;
    text-align: center;
    font-family: "Great Vibes", cursive;
    font-size: 38px;
    line-height: 42px;
    color: var(--ink);
  }
</style>
</head>
<body>
  <main class="advert">
    <svg class="advert-shapes" viewBox="0 0 780 1100" xmlns="http://www.w3.org/2000/svg">
      <defs>
        <linearGradient id="sessionPhotoTone" x1="0" y1="0" x2="1" y2="0.4">
          <stop offset="0" stop-color="#b9c0b4"/>
          <stop offset="0.35" stop-color="#c9b3a0"/>
          <stop offset="0.65" stop-color="#a89888"/>
          <stop offset="1" stop-color="#b78c62"/>
        </linearGradient>
        <linearGradient id="therapistsPhotoTone" x1="0" y1="0" x2="1" y2="0">
          <stop offset="0" stop-color="#e8dcd6"/>
          <stop offset="0.5" stop-color="#d9c8c0"/>
          <stop offset="1" stop-color="#b9d8cf"/>
        </linearGradient>
      </defs>

      <g role="img" aria-label="Photograph of a counselling session: two women seated facing each other, talking">
        <rect x="0" y="0" width="780" height="620" fill="url(#sessionPhotoTone)"/>
      </g>

      <path class="accent-band" d="M0,540 C150,470 380,470 540,430 C660,400 740,330 780,250 L780,1100 L0,1100 Z" fill="var(--sage)"/>
      <path class="cream-panel" d="M0,560 C150,485 380,478 545,448 C670,420 745,350 780,285 L780,1100 L0,1100 Z" fill="var(--cream)"/>

      <g role="img" aria-label="Photograph of two smiling therapists seated in a bright room">
        <path d="M410,838 C480,740 560,650 780,612 L780,722 C660,790 540,830 410,838 Z" fill="url(#therapistsPhotoTone)"/>
      </g>

      <path class="white-panel" d="M410,838 C540,830 660,790 780,722 L780,1100 L318,1100 C345,1020 360,900 410,838 Z" fill="var(--white)"/>
      <path class="contact-panel" d="M0,905 C90,850 220,830 410,838 C360,900 345,1020 318,1100 L0,1100 Z" fill="var(--brown)"/>
    </svg>

    <h1 class="headline">Confidential Therapeutic Services<br>in the Heart of Old Town</h1>

    <p class="intro">We have over <span class="highlight">30 carefully selected, qualified and professional therapists</span> offering a range of services to help individuals, families and couples.</p>

    <section class="contact">
      <p class="hours">Appointments available<br>throughout the day and evening</p>
      <p class="phone">01793 620418</p>
      <p class="address">41 Wellbrook Lane, Old Town,<br>Swindon SN1 7QD</p>
      <p class="website">www.wbtth-swindon.co.uk</p>
    </section>

    <p class="brand-name">Wellbrook Talking Therapies Hub</p>
  </main>
</body>
</html>
```